Business Cards for company that supports physicians that do medical research

Need to create a business card for Qorvel Studies (www.qorvelstudies.example), a company devoted to supporting physicians who conduct medical research. The form of the card should match the message of research and information quest. I have provided the logo of the company as an uploaded file. Designs should be simple and slick aimed at very high end clients.

Target Market(s)

Medical doctors that are also researchers

Industry/Entity Type

Medical

Contact Information for Business Card

Should feature logo and fields for personal info:
Name/title
Phone /email

Font styles to use
Serif
Sans Serif

Requirements
Must have
• Qorvel logo and fields for personal info:
• Name: Bertrand Okonfu
• Title: VP Research and Senior Analyst
• Phone: 555-203-4719
• email: info@qorvelstudies.example
Nice to have
• Interesting cards that I've seen:
• 1- all black/charcoal or very dark background
• 2- Plastic - semi-transparent
• 3- non-standard height-width ratios
• 4- Functional cards -- USB drive incorporated
Should not have
• Too busy; needs to stay very simple

```html
<!DOCTYPE html>
<html lang="en">
<head>
<meta charset="utf-8">
<title>Qorvel Studies – Business Card</title>
<link rel="stylesheet" href="https://fonts.googleapis.com/css2?family=Open+Sans:wght@400;600;700&display=swap">
<style>
  :root {
    --page-bg: #ecebe8;
    --card-dark: #2c2c2d;
    --card-light: #ffffff;
    --brand-green: #4db848;
    --brand-blue: #1b87c9;
    --text-white: #f2f2f2;
    --rule-grey: #bdbdbd;
    --shadow: rgba(0, 0, 0, 0.18);
  }
  * { box-sizing: border-box; margin: 0; padding: 0; }
  html, body {
    width: 1200px;
    height: 900px;
    overflow: hidden;
    background: var(--page-bg);
    font-family: "Open Sans", Arial, sans-serif;
  }
  .canvas {
    position: relative;
    width: 1200px;
    height: 900px;
  }
  .card {
    position: absolute;
    width: 600px;
    height: 343px;
    overflow: hidden;
    box-shadow: 0 10px 28px var(--shadow);
  }

  /* Back of card */
  .card-back {
    left: 500px;
    top: 60px;
    background: var(--card-dark);
  }
  .card-back .wordmark {
    position: absolute;
    left: 0;
    right: 0;
    top: 88px;
    text-align: center;
    color: var(--text-white);
    font-weight: 700;
    font-size: 84px;
    letter-spacing: 1px;
  }
  .card-back .rule {
    position: absolute;
    top: 236px;
    height: 1px;
    background: var(--rule-grey);
  }
  .card-back .rule-left { left: 24px; width: 150px; }
  .card-back .rule-right { right: 24px; width: 150px; }
  .card-back .website {
    position: absolute;
    left: 0;
    right: 0;
    top: 226px;
    text-align: center;
    color: var(--text-white);
    font-size: 14px;
    letter-spacing: 0.5px;
  }

  /* Front of card */
  .card-front {
    left: 100px;
    top: 470px;
    background: var(--card-light);
  }
  .card-front .shapes {
    position: absolute;
    inset: 0;
  }
  .card-front .identity {
    position: absolute;
    left: 70px;
    top: 18px;
  }
  .card-front .person-name {
    color: var(--brand-green);
    font-weight: 700;
    font-size: 17px;
    line-height: 1.2;
  }
  .card-front .person-title {
    color: var(--brand-blue);
    font-size: 13px;
    line-height: 1.3;
  }
  .card-front .contact {
    position: absolute;
    left: 40px;
    top: 196px;
    list-style: none;
    color: var(--brand-blue);
    font-size: 14px;
    line-height: 22px;
  }
  .card-front .contact li {
    display: flex;
    align-items: center;
    gap: 8px;
  }
  .card-front .contact svg { flex: none; }
  .card-front .wordmark {
    position: absolute;
    right: 44px;
    top: 160px;
    color: var(--brand-green);
    font-weight: 700;
    font-size: 38px;
    letter-spacing: 0.5px;
  }
</style>
</head>
<body>
<main class="canvas">

  <section class="card card-back" aria-label="Business card, back">
    <div class="wordmark">Qorvel</div>
    <span class="rule rule-left"></span>
    <span class="website">www.qorvelstudies.example</span>
    <span class="rule rule-right"></span>
  </section>

  <section class="card card-front" aria-label="Business card, front">
    <svg class="shapes" width="600" height="343" viewBox="0 0 600 343" aria-hidden="true">
      <polygon points="0,0 34,0 0,28" fill="var(--brand-blue)"/>
      <polygon points="42,4 62,4 62,28 16,28" fill="var(--brand-green)"/>
      <polygon points="0,258 306,258 292,282 0,282" fill="var(--brand-blue)"/>
      <polygon points="300,290 600,290 600,343 286,343" fill="var(--brand-green)"/>
    </svg>

    <div class="identity">
      <p class="person-name">Bertrand Okonfu</p>
      <p class="person-title">VP Research and Senior Analyst</p>
    </div>

    <ul class="contact">
      <li>
        <svg width="12" height="12" viewBox="0 0 12 12" aria-hidden="true">
          <path d="M2.5 1 L4.5 1 L5.2 3.6 L4 4.6 C4.7 6 6 7.3 7.4 8 L8.4 6.8 L11 7.5 L11 9.5 C11 10.3 10.3 11 9.5 11 C5 11 1 7 1 2.5 C1 1.7 1.7 1 2.5 1 Z" fill="var(--brand-green)"/>
        </svg>
        <span>555-203-4719</span>
      </li>
      <li>
        <svg width="12" height="10" viewBox="0 0 12 10" aria-hidden="true">
          <rect x="0.5" y="0.5" width="11" height="9" fill="var(--brand-green)"/>
          <polyline points="0.5,0.8 6,5.5 11.5,0.8" fill="none" stroke="#ffffff" stroke-width="1.2"/>
        </svg>
        <span>info@qorvelstudies.example</span>
      </li>
    </ul>

    <div class="wordmark">Qorvel Studies</div>
  </section>

</main>
</body>
</html>
```